Pinecrest Travel

We are new traveling company from Italy and looking for a really unique design as soon as possible of the main page.
Travel is an online business. We all do online research before taking a vacation. Since some of us will spend hours researching a trip before finally booking it on a travel website, design is critical.
People looking to travel are going to start with an idea. Some may be browsing for a specific type of trip (river cruise, kayaking, etc.) while others may be looking at specific dates (i.e. February). Still others are considering going to a specific destination such as the Grand Canyon, but all of these visitors are goal-oriented. This type of visitor is frustrated by not finding thle right information easily. This is why travel web design must offer several ways to navigate such as by date, location, activity, cost, etc.
The design should be easy to use for visitors, look fantastic and be easy to update and maintain.
Uploaded some sample pictures but feel free to use your own if it looks good. About colors, blue and white would mix great.

Our future address will be pinecresttravel-example.com

```html
<!DOCTYPE html>
<html lang="en">
<head>
<meta charset="utf-8">
<title>Pinecrest Travel</title>
<link href="https://fonts.googleapis.com/css2?family=Open+Sans:wght@400;600;700&display=swap" rel="stylesheet">
<style>
:root{
  --blue:#1c7fc4;
  --blue-dark:#156aa8;
  --blue-light:#5cc1ef;
  --panel-blue:#2b86c8;
  --green:#1aa35a;
  --green-dark:#138a49;
  --title-blue:#2a8ccd;
  --text:#555;
  --muted:#8a8a8a;
  --grey-box:#f3f3f3;
  --footer:#2b2b2b;
  --footer-bottom:#222;
  --footer-green:#35c46e;
  --white:#fff;
}
*{box-sizing:border-box;margin:0;padding:0}
html,body{width:913px;height:1200px;overflow:hidden}
body{font-family:"Open Sans",sans-serif;color:var(--text);position:relative}
.abs{position:absolute}
.backdrop{left:0;top:0;width:913px;height:962px;
  background:linear-gradient(180deg,#3f8fd6 0%,#6fb2e4 18%,#2ea7b9 33%,#4cc2c4 42%,#e8d2b4 52%,#eec9a4 100%)}
.brand{top:16px;left:0;width:913px;display:flex;justify-content:center;align-items:center;gap:10px}
.brand-dot{width:30px;height:30px;border-radius:50%;background:var(--white)}
.brand-name{font-size:29px;font-weight:700;color:var(--white);letter-spacing:1px}
.sheet{left:71px;top:58px;width:770px;height:852px;background:var(--white)}
.nav{left:79px;top:58px;width:755px;height:34px;background:linear-gradient(#238bd0,#1a74b8);display:flex}
.nav a{color:var(--white);text-decoration:none;font-size:11px;font-weight:600;line-height:34px;text-align:center;white-space:nowrap;border-right:1px solid rgba(255,255,255,.18)}
.nav a.active{background:linear-gradient(#6fcbf3,#48b2e6);color:#1b4e78}
.search{left:686px;top:62px;width:143px;height:25px;background:var(--white);border-radius:2px;font-size:10px;color:#999;padding:6px 9px}
.search svg{position:absolute;right:5px;top:5px}
.hero{left:79px;top:100px;width:755px;height:272px;background:linear-gradient(180deg,#6a9fd0 0%,#a9c8e4 38%,#2fb3c4 45%,#27a3b8 60%,#7a4a34 78%,#5a3424 100%)}
.caption{left:79px;top:372px;width:755px;height:58px;background:#2b2b2b;padding:10px 15px}
.caption h2{font-size:16px;font-weight:400;color:var(--footer-green)}
.caption p{font-size:10px;color:#ccc;margin-top:2px}
.arrows{right:15px;top:20px;display:flex;gap:3px}
.arrows span{width:19px;height:19px;border-radius:50%;background:var(--white);display:flex;align-items:center;justify-content:center}
.section-title{font-size:16px;color:var(--title-blue);font-weight:400}
.title-rule{height:1px;background:#ddd}
.title-rule i{display:block;height:4px;background:var(--title-blue);margin-top:-2px}
.feature-img{left:80px;top:493px;width:243px;height:148px;background:linear-gradient(180deg,#3b9be0 0%,#7dd2ef 40%,#22c5c6 60%,#b2663a 100%)}
.feature-body{left:334px;top:484px;width:302px}
.feature-body h3{font-size:12px;font-weight:600;color:var(--green);line-height:16px}
.date{font-size:10px;color:var(--blue);margin-top:4px}
.feature-body p{font-size:10px;line-height:16px;margin-top:7px}
.shares{display:flex;gap:8px;margin-top:10px;font-size:8px}
.share{display:flex;align-items:center}
.share b{border:1px solid #ccc;border-radius:2px;padding:2px 4px;font-weight:600;color:#335}
.share b.red{background:#e7483b;color:var(--white);border-color:#e7483b}
.share em{font-style:normal;border:1px solid #ccc;padding:2px 3px;margin-left:3px;color:#333}
.grey{left:79px;top:650px;width:562px;height:250px;background:var(--grey-box)}
.card{top:660px;width:176px}
.card .pic{height:98px}
.card h4{font-size:11px;font-weight:400;color:var(--green);margin-top:9px}
.card .date{margin-top:1px}
.card p{font-size:9px;line-height:14px;margin-top:5px}
.pager{left:420px;top:869px;display:flex;gap:3px;align-items:center}
.pager span{width:17px;height:17px;border-radius:2px;background:#d7d7d7;color:#fff;font-size:8px;display:flex;align-items:center;justify-content:center}
.pager span.on{background:#8a8a8a}
.pager i{font-size:8px;color:#999;font-style:normal;margin:0 3px}
.form-panel{left:650px;top:478px;width:184px;height:306px;background:linear-gradient(#3592cd,#2b78bf);border-top:4px solid #1e5f9a;padding:21px 10px 0}
.field{background:var(--white);height:27px;border-radius:2px;font-size:10px;color:#666;padding:6px 9px;margin-bottom:6px;position:relative}
.field.msg{height:74px}
.submit{float:right;background:var(--white);color:var(--blue-dark);font-weight:700;font-size:11px;padding:6px 9px;border-radius:2px;margin-top:2px}
.offer{left:650px;top:790px;width:184px;height:110px;background:linear-gradient(90deg,#e8f3fb 0%,#cfe7f6 55%,#b9a172 100%)}
.offer h3{position:absolute;left:12px;top:21px;font-size:19px;font-weight:600;color:#222;line-height:23px}
.offer .more{position:absolute;left:12px;top:73px;background:var(--green);color:var(--white);font-size:9px;padding:3px 8px;border-radius:2px}
.service{top:918px;height:35px;width:187px;background:var(--white);display:flex;align-items:center;justify-content:center;gap:10px;font-size:14px;color:var(--green);font-weight:400}
.footer{left:0;top:962px;width:913px;height:192px;background:var(--footer)}
.fcol{top:983px}
.fcol h5{font-size:13px;font-weight:400;color:var(--footer-green);margin-bottom:12px}
.fcol li{list-style:none;font-size:10px;color:#e5e5e5;line-height:19px}
.fcol p{font-size:10px;color:#ccc;line-height:14px;width:190px}
.finput{background:#eee;height:20px;width:186px;border-radius:2px;font-size:9px;color:#444;padding:4px 11px;margin-top:6px}
.subscribe{background:var(--green-dark);color:var(--white);font-size:9px;padding:5px 10px;border-radius:2px;display:inline-block;margin:7px 0 0 117px}
.social li{display:flex;align-items:center;gap:7px;line-height:25px}
.social i{width:19px;height:19px;border-radius:50%;background:#eee}
.bottom{left:0;top:1154px;width:913px;height:46px;background:var(--footer-bottom);font-size:9px;color:#aaa;text-align:center;line-height:46px}
</style>
</head>
<body>
<div class="abs backdrop" role="img" aria-label="Tropical beach with turquoise sea, surf and sand"></div>

<header class="abs brand"><span class="brand-dot"></span><span class="brand-name">PINECREST TRAVEL</span></header>

<div class="abs sheet"></div>

<nav class="abs nav">
  <a class="active" style="width:62px">HOME</a><a style="width:86px">ABOUT US</a><a style="width:78px">SERVICES</a><a style="width:105px">TRAVEL GUIDE</a><a style="width:169px">POPULAR VACTION AREAS</a><a style="width:94px">CONTACT US</a>
</nav>
<div class="abs search">Search
  <svg width="14" height="14" viewBox="0 0 14 14"><circle cx="6" cy="6" r="4.5" fill="none" stroke="#999" stroke-width="1.6"/><line x1="9.3" y1="9.3" x2="13" y2="13" stroke="#999" stroke-width="1.8"/></svg>
</div>

<div class="abs hero" role="img" aria-label="Wooden jetty with lounge chairs and canopies over a turquoise sea"></div>
<div class="abs caption">
  <h2>Proin facilisis elementum</h2>
  <p>Praesent a enim venenatis, interdum lorem vel, laoreet ipsum. Nullam sem ipsum, volutpat vel nisl ut, commodo cursus tellus.</p>
  <div class="abs arrows">
    <span><svg width="8" height="8" viewBox="0 0 8 8"><path d="M6 1L2 4l4 3z" fill="#333"/></svg></span>
    <span><svg width="8" height="8" viewBox="0 0 8 8"><path d="M2 1l4 3-4 3z" fill="#333"/></svg></span>
  </div>
</div>

<div class="abs" style="left:79px;top:452px;width:562px">
  <h2 class="section-title">RECENT VACTIONS</h2>
  <div class="title-rule" style="margin-top:4px"><i style="width:143px"></i></div>
</div>

<div class="abs feature-img" role="img" aria-label="Long wooden pier leading to a hut over clear turquoise water"></div>
<article class="abs feature-body">
  <h3>Nunc semper ultricies augue quis condimentum aptent taciti sociosqu ad litora torquent</h3>
  <div class="date">May 9, 2014</div>
  <p>Etiam a tempus erat. Pellentesque in purus porta, volutpat enim sed, cursus magna. Donec lorem ipsum, tristique quis faucibus et, viverra at sapien. Duis eleifend mi non magna pel-lentesque lobortis vehicula nulla elit.</p>
  <div class="shares">
    <span class="share"><b>Like</b><em>3k</em></span>
    <span class="share"><b>Post</b><em>316</em></span>
    <span class="share"><b>+1</b><em>81</em></span>
    <span class="share"><b class="red">Share</b><em>4.6K</em></span>
  </div>
</article>

<div class="abs grey"></div>
<article class="abs card" style="left:88px">
  <div class="pic" role="img" aria-label="Couple seated overlooking white hillside village and sea" style="background:linear-gradient(160deg,#d9d0c0,#b9885a 45%,#c8332c 75%,#4a3a30)"></div>
  <h4>Proin facilisis elementum lorem</h4><div class="date">May 9, 2014</div>
  <p>Donec lorem ipsum, tristique quis faucibus et, viverra at sapien. Duis eleifend mi non magna pellentesque lobortis vehicula nulla elit.</p>
</article>
<article class="abs card" style="left:271px">
  <div class="pic" role="img" aria-label="Resort pool with palm trees and sun loungers" style="background:linear-gradient(180deg,#3d7fc0,#9cc6e6 45%,#3a8a4a 60%,#7fd3e6 80%,#e7e2d6)"></div>
  <h4>Proin facilisis elementum lorem</h4><div class="date">May 9, 2014</div>
  <p>Donec lorem ipsum, tristique quis faucibus et, viverra at sapien. Duis eleifend mi non magna pellentesque lobortis vehicula nulla elit.</p>
</article>
<article class="abs card" style="left:454px">
  <div class="pic" role="img" aria-label="Traveller silhouetted against a golden sunset over temples" style="background:linear-gradient(180deg,#f0b040,#d07818 55%,#5a2a10)"></div>
  <h4>Proin facilisis elementum lorem</h4><div class="date">May 9, 2014</div>
  <p>Donec lorem ipsum, tristique quis faucibus et, viverra at sapien. Duis eleifend mi non magna pellentesque lobortis vehicula nulla elit.</p>
</article>
<div class="abs pager">
  <span class="on">1</span><span>2</span><span>3</span><span>4</span><span>5</span><span>6</span><span>7</span><span>8</span><span>»</span><i>…</i><span>»»</span>
</div>

<div class="abs" style="left:650px;top:452px;width:184px">
  <h2 class="section-title">FIND A VACATION</h2>
</div>
<form class="abs form-panel">
  <div class="field">Name</div>
  <div class="field">Phone</div>
  <div class="field">E-mail</div>
  <div class="field">Date &amp; Time
    <svg style="position:absolute;right:6px;top:5px" width="18" height="16" viewBox="0 0 18 16"><rect x="1" y="2" width="16" height="13" fill="#f4f4f4" stroke="#aaa"/><rect x="1" y="2" width="16" height="3" fill="#bbb"/><g fill="#ccc"><rect x="3" y="7" width="2" height="2"/><rect x="7" y="7" width="2" height="2"/><rect x="11" y="7" width="2" height="2"/><rect x="3" y="11" width="2" height="2"/><rect x="7" y="11" width="2" height="2"/></g></svg>
  </div>
  <div class="field">Vacation Type
    <svg style="position:absolute;right:8px;top:11px" width="9" height="6" viewBox="0 0 9 6"><path d="M0 0h9L4.5 6z" fill="#888"/></svg>
  </div>
  <div class="field msg">Message</div>
  <div class="submit">SUBMIT</div>
</form>

<aside class="abs offer" role="img" aria-label="Special offer banner with a shopping bag of world landmarks">
  <h3>Special<br>Offer</h3>
  <span class="more">Read More</span>
</aside>

<div class="abs service" style="left:72px">
  <svg width="26" height="16" viewBox="0 0 26 16"><rect x="1" y="1" width="24" height="14" fill="none" stroke="#1aa35a" stroke-width="2"/><rect x="5" y="4" width="16" height="8" fill="#1aa35a"/></svg>TICKET BOOKING</div>
<div class="abs service" style="left:266px">
  <svg width="22" height="22" viewBox="0 0 22 22"><rect x="2" y="8" width="8" height="14" fill="#1aa35a"/><rect x="10" y="2" width="10" height="20" fill="#1aa35a"/><g fill="#fff"><rect x="12" y="5" width="2" height="2"/><rect x="16" y="5" width="2" height="2"/><rect x="12" y="10" width="2" height="2"/><rect x="16" y="10" width="2" height="2"/><rect x="4" y="12" width="2" height="2"/></g></svg>HOTEL BOOKING</div>
<div class="abs service" style="left:460px">
  <svg width="28" height="16" viewBox="0 0 28 16"><path d="M2 9l4-6h14l5 6h1v4H2z" fill="#1aa35a"/><circle cx="8" cy="13" r="3" fill="#1aa35a" stroke="#fff"/><circle cx="21" cy="13" r="3" fill="#1aa35a" stroke="#fff"/></svg>RENTAL CARS</div>
<div class="abs service" style="left:654px">
  <svg width="16" height="24" viewBox="0 0 16 24"><rect x="5" y="1" width="6" height="4" fill="none" stroke="#1aa35a" stroke-width="2"/><rect x="2" y="5" width="12" height="16" rx="2" fill="#1aa35a"/><circle cx="5" cy="22" r="1.5" fill="#1aa35a"/><circle cx="11" cy="22" r="1.5" fill="#1aa35a"/></svg>TOUR PACKAGES</div>

<footer class="abs footer"></footer>
<div class="abs fcol" style="left:77px"><h5>Quick Links</h5><ul><li>Home</li><li>About us</li><li>Services</li><li>Travel Guide</li><li>Popular Vaction Areas</li><li>Contact us</li></ul></div>
<div class="abs fcol" style="left:218px"><h5>Browse Categories</h5><ul><li>World Travel</li><li>Vegas Travel</li><li>US Travel</li><li>Travel Maps</li><li>Travel Insurance</li><li>Travel Agent</li></ul></div>
<div class="abs fcol" style="left:377px"><h5>Browse Categories</h5><ul><li>Travel Accessories</li><li>Travel</li><li>RV Travel</li><li>Luxury Travel</li><li>Discount Travel</li><li>Europe Travel</li></ul></div>
<div class="abs fcol" style="left:523px"><h5>Newsletters Sign Up</h5>
  <p>Sign up for our daily email by entering your information below</p>
  <div class="finput">Your name</div><div class="finput">Email address</div>
  <span class="subscribe">SUBSCRIBE</span>
</div>
<div class="abs fcol social" style="left:737px"><h5>Connect With Us</h5><ul><li><i></i>Friendcircle</li><li><i></i>Chirpline</li><li><i></i>Worknet</li></ul></div>

<div class="abs bottom">Copyright © 2014 &nbsp;Pinecrest Travel. &nbsp;All rights reserved.</div>
</body>
</html>
```